Oil and Gas Exploration and Production company needs a business card design

We need a business card design using our logo and colors in the logo. We want a mainstream design.

```html
<!DOCTYPE html>
<html lang="en">
<head>
<meta charset="utf-8">
<title>Vanta Oil &amp; Gas – Business Card</title>
<link rel="stylesheet" href="https://fonts.googleapis.com/css2?family=Arimo:wght@400;700&display=swap">
<style>
  :root {
    --ink: #0d0d0d;
    --paper: #ffffff;
    --gold: #e3c23f;
    --gold-deep: #c9a72c;
    --backdrop: #ece9e3;
    --muted-white: #f1f1f1;
  }
  html, body {
    margin: 0;
    padding: 0;
    width: 1200px;
    height: 780px;
    overflow: hidden;
    background: var(--backdrop);
    font-family: "Arimo", Arial, sans-serif;
  }
  .sheet {
    width: 1200px;
    height: 780px;
    display: flex;
    align-items: center;
    justify-content: center;
    gap: 40px;
  }
  .card {
    position: relative;
    width: 540px;
    height: 309px;
    overflow: hidden;
    box-shadow: 0 10px 28px rgba(0,0,0,0.22);
  }
  .card-shapes {
    position: absolute;
    inset: 0;
    width: 100%;
    height: 100%;
  }
  .brand {
    position: absolute;
    left: 34px;
    top: 132px;
    display: flex;
    align-items: center;
    gap: 10px;
  }
  .brand-dot {
    width: 22px;
    height: 22px;
    border-radius: 50%;
    background: var(--ink);
  }
  .brand-name {
    font-weight: 700;
    font-size: 26px;
    color: var(--ink);
    letter-spacing: 0.2px;
  }
  .contact {
    position: absolute;
    right: 26px;
    top: 44px;
    text-align: right;
    color: var(--paper);
  }
  .person-name {
    font-weight: 700;
    font-size: 19px;
    margin: 0;
  }
  .person-role {
    font-size: 13px;
    color: var(--gold);
    margin: 3px 0 40px;
  }
  .contact-list {
    list-style: none;
    margin: 0;
    padding: 0;
  }
  .contact-item {
    display: flex;
    align-items: center;
    justify-content: flex-end;
    gap: 10px;
    font-size: 12.5px;
    margin-bottom: 10px;
  }
  .contact-icon {
    width: 20px;
    height: 20px;
    flex: none;
  }
</style>
</head>
<body>
<main class="sheet">

  <!-- Front of card -->
  <section class="card card-front" aria-label="Business card front">
    <svg class="card-shapes" viewBox="0 0 540 309" preserveAspectRatio="none" aria-hidden="true">
      <rect width="540" height="309" fill="var(--paper)"/>
      <path d="M292 0 C 300 120 262 230 160 309 L540 309 L540 0 Z" fill="var(--gold)"/>
      <path d="M304 0 C 312 125 280 235 200 309 L540 309 L540 0 Z" fill="var(--paper)"/>
      <path d="M310 0 C 318 125 288 235 210 309 L540 309 L540 0 Z" fill="var(--ink)"/>
    </svg>

    <div class="brand">
      <span class="brand-dot"></span>
      <span class="brand-name">Vanta Oil &amp; Gas</span>
    </div>

    <div class="contact">
      <p class="person-name">Marco Reyes</p>
      <p class="person-role">President &amp; CEO</p>
      <ul class="contact-list">
        <li class="contact-item">
          <span>(321) 555 0147</span>
          <svg class="contact-icon" viewBox="0 0 20 20" aria-hidden="true">
            <circle cx="10" cy="10" r="9" fill="none" stroke="var(--gold)" stroke-width="1.4"/>
            <path d="M7 5.5 L8.6 5.5 L9.3 7.8 L8.3 8.7 Q9.3 10.9 11.3 11.7 L12.2 10.7 L14.5 11.4 L14.5 13 Q14 14.2 12.6 14.1 Q7.4 13.2 5.9 7.4 Q5.8 6 7 5.5 Z" fill="var(--gold)"/>
          </svg>
        </li>
        <li class="contact-item">
          <span>hello@vantaenergy.com</span>
          <svg class="contact-icon" viewBox="0 0 20 20" aria-hidden="true">
            <circle cx="10" cy="10" r="9" fill="none" stroke="var(--gold)" stroke-width="1.4"/>
            <rect x="5.5" y="6.8" width="9" height="6.4" fill="var(--gold)"/>
            <path d="M5.5 6.8 L10 10.4 L14.5 6.8" fill="none" stroke="var(--ink)" stroke-width="0.9"/>
          </svg>
        </li>
        <li class="contact-item">
          <span>www.vantaenergy.com</span>
          <svg class="contact-icon" viewBox="0 0 20 20" aria-hidden="true">
            <circle cx="10" cy="10" r="9" fill="none" stroke="var(--gold)" stroke-width="1.4"/>
            <circle cx="10" cy="10" r="5" fill="none" stroke="var(--gold)" stroke-width="1.1"/>
            <ellipse cx="10" cy="10" rx="2.2" ry="5" fill="none" stroke="var(--gold)" stroke-width="1"/>
            <path d="M5 10 H15" stroke="var(--gold)" stroke-width="1"/>
          </svg>
        </li>
      </ul>
    </div>
  </section>

  <!-- Back of card -->
  <section class="card card-back" aria-label="Business card back">
    <svg class="card-shapes" viewBox="0 0 540 309" preserveAspectRatio="none" aria-hidden="true">
      <rect width="540" height="309" fill="var(--ink)"/>
      <path d="M300 0 L540 0 L540 250 Z" fill="var(--muted-white)"/>
      <path d="M0 309 L0 230 L150 309 Z" fill="var(--muted-white)"/>
      <path d="M60 0 L118 0 L70 309 L12 309 Z" fill="var(--gold-deep)"/>
    </svg>
  </section>

</main>
</body>
</html>
```